Brightwave Charters website

Looking to have a new, interactive website built on Wordpress and hosted by hostorra. Our current site was made and is hosted by plim and has been up and running for 8 years. Would like to replace as seamlessly as possible. Attached are general ideas for the site as well as requirements. Would like to showcase our charter options and information on the home page with Our Charters, FAQ and Gallery as follow up pages. Would like to be created in Wordpress and HTTPS

Target Market(s)

Vacationing tourists visiting Siesta Key

Industry/Entity Type

Boat Charters

Number of Pages Required

1 page

Requirements
Must have
• Website must be secure, HTTPS not HTTP . . Use webp images throughout the entire site. Info for the home page was uploaded on 3 seperate pages labeled home1, home2 and home3. Need the bottom, above footer, to show What Our Customers Say About Us with reviews from Plentora, Zentrix and QM. Homepage to have all 6 charter options and info provided on the attached docx labeled home1, home2 and home3 . If we can get the 3 pages following the home page (Our Charters,FAQ and Gallery) I had also attached brief summaries for those pages. Install these Plug-ins, MERV, Slotwise (free), Blockforge plugin. Any other plugin needs to be approved by us

```html
<!DOCTYPE html>
<html lang="en">
<head>
<meta charset="utf-8">
<title>Brightwave Charters – Private Boat Tours on Siesta Key</title>
<link href="https://fonts.googleapis.com/css2?family=Playfair+Display:wght@700;800&family=Noto+Serif:wght@400;600;700&family=Roboto:wght@400;500&display=swap" rel="stylesheet">
<style>
:root{
  --orange:#f28a1f;
  --orange-light:#f7a43c;
  --blue:#2f8acb;
  --navy:#1f2f45;
  --band:#2c6488;
  --band-dark:#1f4e6e;
  --ink:#2b2b2b;
  --muted:#444;
  --line:#d9dde2;
  --mist:#e5eef6;
  --white:#fff;
}
*{box-sizing:border-box;margin:0;padding:0}
html,body{width:1200px;height:3526px;overflow:hidden;background:var(--white)}
body{position:relative;font-family:"Noto Serif",serif;color:var(--ink)}
.abs{position:absolute}
.heading{font-family:"Playfair Display",serif;font-weight:800;color:var(--blue);text-transform:uppercase}
.rule{display:block;width:34px;height:3px;background:var(--orange);border-radius:2px}
.btn{display:inline-block;background:linear-gradient(90deg,var(--orange),var(--orange-light));color:var(--white);font-family:"Noto Serif",serif;font-weight:700;font-size:14px;text-transform:uppercase;border-radius:22px;padding:10px 18px;text-decoration:none;letter-spacing:.2px}

/* header */
.site-header{left:0;top:0;width:1200px;height:89px;background:var(--white);z-index:5}
.brand-badge{left:98px;top:0;width:150px;height:115px;background:var(--white);border-radius:0 0 75px 75px;display:flex;align-items:center;justify-content:center;text-align:center;z-index:6}
.brand-badge span{font-family:"Noto Serif",serif;font-weight:700;color:var(--blue);font-size:15px;line-height:1.2}
.main-nav{left:326px;top:38px;display:flex;gap:48px;font-size:15px;color:var(--navy)}
.main-nav a{color:var(--navy);text-decoration:none}
.main-nav a.active{color:var(--orange);border-bottom:1px solid var(--orange)}
.call{left:822px;top:30px;display:flex;align-items:center;gap:12px}
.call-icon{width:36px;height:36px;border-radius:50%;background:var(--orange);display:flex;align-items:center;justify-content:center}
.call-text{font-size:14px;line-height:1.35}
.call-text b{color:var(--orange);font-weight:600;display:block}

/* hero */
.hero{left:0;top:89px;width:1200px;height:560px;background:linear-gradient(180deg,#5a7f93 0%,#3c6a8a 40%,#2c5778 70%,#7a5a3a 100%)}
.hero-title{left:105px;top:258px;font-family:"Playfair Display",serif;font-weight:700;color:var(--white);font-size:56px;line-height:59px;text-transform:uppercase}
.hero .btn{}
.hero-cta{left:104px;top:464px;font-size:15px;padding:12px 20px}

/* charters */
.section-title{left:0;width:1200px;text-align:center}
.charter-card{width:324px;height:343px;border:1px solid var(--line);border-radius:12px;background:var(--white);text-align:center}
.charter-photo{position:absolute;left:10px;top:10px;width:303px;height:197px;border-radius:10px}
.charter-card h3{position:absolute;left:0;top:236px;width:100%;font-family:"Noto Serif",serif;font-weight:700;font-size:20px;color:var(--navy)}
.charter-card .btn{position:absolute;left:50%;top:276px;transform:translateX(-50%);padding:8px 17px}

/* band */
.book-band{left:0;top:1540px;width:1200px;height:450px}
.book-title{left:0;top:1736px;width:1200px;text-align:center;font-family:"Playfair Display",serif;font-weight:700;font-size:32px;color:var(--white);text-transform:uppercase}
.book-sub{left:0;top:1812px;width:1200px;text-align:center;color:var(--white);font-size:18px}

/* about */
.about-text{left:102px;top:2190px;width:446px;font-size:15px;line-height:26px;color:var(--muted)}
.about-text p+p{margin-top:10px}
.about-photo{left:686px;top:2094px;width:383px;height:383px;border-radius:50%;background:linear-gradient(180deg,#e9a46a 0%,#f1c58d 35%,#6e8ba0 60%,#3f5d73 100%)}

/* reviews */
.review{width:297px;background:var(--white);border:1px solid var(--line);border-radius:12px;padding:18px 20px}
.review.featured{box-shadow:0 4px 18px rgba(0,0,0,.18);border-color:transparent}
.review-head{display:flex;gap:14px;align-items:center}
.avatar{width:60px;height:60px;border-radius:50%;flex:none}
.review-name{font-family:"Noto Serif",serif;font-size:18px;color:var(--blue)}
.review-meta{font-family:"Roboto",sans-serif;font-size:12px;font-weight:500;color:#222;margin-top:2px}
.review-body{font-size:13px;line-height:22px;color:var(--muted);margin-top:16px}
.source{display:flex;align-items:center;gap:5px;font-family:"Roboto",sans-serif;font-size:13px;font-weight:500;color:#222;margin-top:6px}
.source i{width:14px;height:14px;border-radius:50%;background:#34c28d;display:inline-block}
.source.qm{color:#3b5a9a;font-size:18px;font-weight:500;display:block}
.stars{color:#f2c200;font-size:11px;letter-spacing:1px}

/* footer */
.footer-brand{left:105px;top:3240px;width:222px;height:200px;display:flex;flex-direction:column;align-items:center;justify-content:center;gap:12px}
.footer-brand .dot{width:70px;height:70px;border-radius:50%;background:var(--orange)}
.footer-brand span{font-family:"Noto Serif",serif;font-weight:700;font-size:22px;color:var(--blue);text-align:center;line-height:1.2}
.footer-col h4{font-family:"Playfair Display",serif;font-weight:700;font-size:25px;color:var(--blue);margin-bottom:12px}
.footer-col ul{list-style:none;font-size:15px;line-height:29px;color:var(--navy)}
.footer-col ul li:first-child{font-weight:700}
.contact-list{font-size:15px;line-height:22px;color:var(--navy)}
.contact-list p{margin-bottom:6px}
.social{display:flex;gap:10px;font-size:14px;font-weight:600;color:var(--navy)}
.social span{border:1px solid var(--navy);border-radius:4px;padding:2px 6px}
.footer-rule{left:103px;top:3487px;width:993px;height:1px;background:#555}
.copyright{left:0;top:3500px;width:1200px;text-align:center;font-family:"Roboto",sans-serif;font-size:11px;color:#333}
</style>
</head>
<body>

<!-- hero -->
<section class="abs hero" role="img" aria-label="Photo of a family relaxing on a yellow speedboat on calm water at sunset"></section>
<svg class="abs" style="left:0;top:590px" width="1200" height="70" viewBox="0 0 1200 70" aria-hidden="true">
  <path d="M0 50 C200 20 380 10 620 40 C840 65 1000 40 1200 20 L1200 70 L0 70Z" fill="#fff"/>
</svg>
<h1 class="abs hero-title">Best Private<br>Boat Tour<br>On Siesta Key</h1>
<a class="abs btn hero-cta" href="#">Get Started</a>

<header class="abs site-header"></header>
<div class="abs brand-badge"><span>Brightwave<br>Charters</span></div>
<nav class="abs main-nav">
  <a class="active" href="#">Home</a><a href="#">Our Charters</a><a href="#">FAQ</a><a href="#">Gallery</a><a href="#">Contact</a>
</nav>
<div class="abs call">
  <span class="call-icon"><svg width="16" height="16" viewBox="0 0 24 24"><path fill="#fff" d="M6.6 10.8c1.4 2.8 3.8 5.1 6.6 6.6l2.2-2.2c.3-.3.7-.4 1-.2 1.1.4 2.3.6 3.6.6.6 0 1 .4 1 1V20c0 .6-.4 1-1 1C10.6 21 3 13.4 3 4c0-.6.4-1 1-1h3.5c.6 0 1 .4 1 1 0 1.3.2 2.5.6 3.6.1.3 0 .7-.2 1z"/></svg></span>
  <div class="call-text"><b>CALL US TODAY!</b>555/014-2870</div>
</div>

<!-- charters -->
<h2 class="abs section-title heading" style="top:738px;font-size:32px">Our Charter</h2>
<span class="abs rule" style="left:583px;top:781px"></span>

<article class="abs charter-card" style="left:103px;top:823px"><div class="charter-photo" role="img" aria-label="Dolphin leaping in a boat wake" style="background:linear-gradient(180deg,#7fa7c7,#3f6f95 55%,#e9f0f5)"></div><h3>Dolphin/Wildlife Tours</h3><a class="btn" href="#">Read More</a></article>
<article class="abs charter-card" style="left:438px;top:823px"><div class="charter-photo" role="img" aria-label="Friends sitting on the bow of a boat at a sandbar" style="background:linear-gradient(180deg,#5d8ea8,#8a9a6e 50%,#d9d2c4)"></div><h3>Sandbar Fun</h3><a class="btn" href="#">Read More</a></article>
<article class="abs charter-card" style="left:773px;top:823px"><div class="charter-photo" role="img" aria-label="Group snorkeling in clear turquoise water" style="background:linear-gradient(180deg,#6fc4c0,#3a9b99 60%,#4c8d8a)"></div><h3>Snorkeling</h3><a class="btn" href="#">Read More</a></article>
<article class="abs charter-card" style="left:103px;top:1179px"><div class="charter-photo" role="img" aria-label="Guest holding a large seashell in shallow water" style="background:linear-gradient(180deg,#7cc0a4,#4ba184 60%,#6a8f7a)"></div><h3>Shelling &amp; Beaches</h3><a class="btn" href="#">Read More</a></article>
<article class="abs charter-card" style="left:438px;top:1179px"><div class="charter-photo" role="img" aria-label="Group of friends at a waterfront tiki bar" style="background:linear-gradient(180deg,#9ec3e0,#7d8f8a 55%,#c9bba2)"></div><h3>Tiki Bar Crawl</h3><a class="btn" href="#">Read More</a></article>
<article class="abs charter-card" style="left:773px;top:1179px"><div class="charter-photo" role="img" aria-label="Guests on a boat during a sunset cruise" style="background:linear-gradient(180deg,#e9a56b,#f0c690 40%,#6b8aa2 70%,#3e5a70)"></div><h3>Sunset Cruise</h3><a class="btn" href="#">Read More</a></article>

<!-- book band -->
<svg class="abs book-band" viewBox="0 0 1200 450" role="img" aria-label="Faded photo of charter guests in the water behind a blue band">
  <defs><linearGradient id="bandFill" x1="0" y1="0" x2="0" y2="1"><stop offset="0" stop-color="#2f6a8e"/><stop offset="1" stop-color="#22597c"/></linearGradient></defs>
  <path d="M0 60 C220 20 420 20 620 35 C820 50 1000 0 1200 15 L1200 360 C1000 430 760 370 560 400 C340 430 160 400 0 420Z" fill="url(#bandFill)"/>
</svg>
<h2 class="abs book-title">Book Your Siesta Key Boat Charter Today!</h2>
<span class="abs" style="left:583px;top:1788px;width:34px;height:2px;background:#fff"></span>
<p class="abs book-sub">Dolphin Tours, Snorkeling, Sandbars, Tiki Bars, Shelling, Sunsets</p>
<a class="abs btn" href="#" style="left:538px;top:1858px;padding:9px 17px">Book Now</a>

<!-- about -->
<h2 class="abs heading" style="left:102px;top:2087px;font-size:34px;line-height:40px">About<br>Brightwave Charters</h2>
<span class="abs rule" style="left:103px;top:2170px"></span>
<div class="abs about-text">
  <p>Welcome to the BEST private charter on and around Siesta Key! Whether you live on Siesta Key, Sarasota or are one of our many welcome visitors… we want you to enjoy the day on the crystal clear waters and pristine beaches. My name is Cal Brenner and I look forward to being your Captain for the day. My goal is to ensure a safe and fun time on the water.</p>
  <p>I will work hard to create unforgettable memories with a charter that you, your family and friends will remember.</p>
</div>
<a class="abs btn" href="#" style="left:102px;top:2422px;padding:9px 17px">Read More</a>
<div class="abs about-photo" role="img" aria-label="Captain and guests on a boat at sunset"></div>

<!-- reviews -->
<svg class="abs" style="left:0;top:2540px" width="1200" height="640" viewBox="0 0 1200 640" aria-hidden="true">
  <path d="M0 25 C200 10 380 0 560 12 C760 26 980 40 1200 6 L1200 640 L0 640Z" fill="#e5eef6"/>
</svg>
<h2 class="abs section-title heading" style="top:2650px;font-size:32px;line-height:40px">What Our Charter Guests Have To<br>Say About Us</h2>
<span class="abs rule" style="left:583px;top:2738px"></span>

<article class="abs review" style="left:103px;top:2742px;height:270px">
  <div class="review-head"><div class="avatar" role="img" aria-label="Reviewer photo" style="background:#5a4638"></div><div><div class="review-name">Tomas Reyes</div><div class="review-meta">Oct 2024 • Couples</div></div></div>
  <p class="review-body">Cal took my husband and I out for an afternoon to decompress from hurricane cleanup and evacuation.His boat was immaculate and very comfortable for an afternoon cruise to Venice .</p>
  <div class="source"><i></i>Plentora</div>
</article>
<article class="abs review featured" style="left:452px;top:2806px;height:270px">
  <div class="review-head"><div class="avatar" role="img" aria-label="Reviewer photo" style="background:#4a6f9a"></div><div><div class="review-name">Seashell_77</div><div class="review-meta">Jun 2024 • Family</div></div></div>
  <p class="review-body">There is not a better charter to take in Siesta Key than Brightwave Charters with Cal! He is a great captain that will make sure you have the best experience possible. Always prompt answers with any</p>
  <div class="source qm">QM<div class="stars">★★★★★</div></div>
</article>
<article class="abs review" style="left:800px;top:2742px;height:270px">
  <div class="review-head"><div class="avatar" role="img" aria-label="Reviewer photo" style="background:#a45a3a"></div><div><div class="review-name">Laura P</div><div class="review-meta">Brightwave Charters is a MUST!!</div></div></div>
  <p class="review-body">We cannot say enough great things about Rhea &amp; Cal! This was our first time visiting Siesta Key and they were great from our arrival to the airport! Rhea made sure we had a ride to and from the airport, to the</p>
  <div class="source"><i></i>Plentora</div>
</article>

<!-- footer -->
<div class="abs footer-brand"><span class="dot"></span><span>Brightwave<br>Charters</span></div>
<div class="abs footer-col" style="left:420px;top:3252px">
  <h4>Quick links</h4>
  <ul><li>Home</li><li>Our Charters</li><li>FAQ</li><li>Gallery</li><li>Contact</li></ul>
</div>
<div class="abs footer-col" style="left:612px;top:3252px">
  <h4>Contact Us</h4>
  <div class="contact-list">
    <p>Capt Cal or Rhea :<br>555-014-2870</p>
    <p>Email :<br>Cal@brightwavecharters.com</p>
    <p>Address :<br>1420 Harbor Light Rd, Siesta Key</p>
  </div>
</div>
<div class="abs footer-col" style="left:876px;top:3252px">
  <h4>Follow Us</h4>
  <div class="social"><span>Snapgram</span><span>Chirp</span><span>QM</span></div>
</div>
<div class="abs footer-rule"></div>
<p class="abs copyright">© 2024 Brightwave Charters LLC | All rights reserved.</p>

</body>
</html>
```